Makers' Hollow - Landing page for small and large screen

Makers’ Hollow gives you the space you need to take your side project from idea to reality.

With three days of focused work, it’s a place for you iron out the details of your business idea away from the distractions of the city.

The full copy and structure is here:
https://www.makershollow.co.uk/landing

What it needs, a touch of colour.

Target Market(s)

25-35 working in digital industry, software developer, a UI or UX designer

Number of Pages Required

1 page

Font styles to use
Sans Serif

Colors
0292cd
33b8a4
86cfc6
fdf9cf
ec1f27

Requirements
Should not have
• gradients or too much images

```html
<!DOCTYPE html>
<html lang="en">
<head>
<meta charset="utf-8">
<title>Makers’ Hollow</title>
<link rel="stylesheet" href="https://fonts.googleapis.com/css2?family=Lato:wght@400;700;900&display=swap">
<style>
:root{
  --blue:#0a86cc;
  --footer-blue:#0b79c1;
  --teal:#2eac92;
  --red:#e31b25;
  --ink:#2b2b2b;
  --grey:#5d5d5d;
  --white:#ffffff;
  --mist:#f2f5f8;
}
*{margin:0;padding:0;box-sizing:border-box}
html,body{width:1200px;height:2995px;overflow:hidden}
body{font-family:'Lato',sans-serif;background:var(--white);color:var(--ink);position:relative}
.abs{position:absolute}

/* Hero */
.hero{position:absolute;left:0;top:0;width:1200px;height:690px;overflow:hidden}
.hero-photo{position:absolute;inset:0;background:linear-gradient(100deg,#6d5648 0%,#8a7666 25%,#5a5a5e 50%,#a0704c 78%,#c27a45 100%)}
.hero-shade{position:absolute;inset:0;background:linear-gradient(180deg,rgba(0,0,0,.25),rgba(0,0,0,.15) 60%,rgba(0,0,0,.3))}
.brand{position:absolute;left:144px;top:30px;color:var(--white)}
.brand-name{font-size:31px;font-weight:900;letter-spacing:.2px}
.brand-tag{font-size:14px;margin-top:2px;padding-left:3px}
.main-nav{position:absolute;top:44px;left:496px;display:flex;gap:34px;color:var(--white);font-size:17px;font-weight:700}
.hero-title{position:absolute;top:254px;width:100%;text-align:center;color:var(--white);font-size:45px;font-weight:700}
.hero-sub{position:absolute;top:318px;width:100%;text-align:center;color:var(--white);font-size:21px;line-height:28px}
.hero-arrow{position:absolute;top:280px;width:52px;height:52px;border-radius:50%;background:rgba(210,210,210,.75);border:0}
.hero-dots{position:absolute;top:552px;left:570px;display:flex;gap:8px}
.dot{width:14px;height:14px;border-radius:50%;border:2px solid var(--white)}
.dot.on{background:var(--white)}
.hero-curve{position:absolute;left:0;top:600px}

/* Intro */
.intro-title{position:absolute;top:716px;width:100%;text-align:center;color:var(--blue);font-size:32px;font-weight:700;line-height:38px}
.intro-copy{position:absolute;top:820px;width:100%;text-align:center;color:var(--grey);font-size:16.5px;line-height:30px}
.btn-more{position:absolute;left:496px;top:1002px;width:190px;height:58px;border:2px solid var(--red);border-radius:30px;color:var(--red);font-weight:700;font-size:18px;display:flex;align-items:center;justify-content:center}

/* Benefits */
.benefits{position:absolute;left:0;top:1148px;width:1200px;height:480px;background:var(--teal)}
.benefits-title{position:absolute;top:54px;width:100%;text-align:center;color:var(--white);font-size:32px;font-weight:700}
.benefit{position:absolute;width:212px;border:2.5px solid var(--white);border-radius:4px;color:var(--white);text-align:center;font-weight:700;font-size:16px;line-height:21px;padding:0 16px}
.benefit svg{display:block;margin:0 auto 12px}
.chev{position:absolute;top:240px}

/* Stay */
.stay{position:absolute;left:0;top:1628px;width:1200px;height:490px;background:var(--mist)}
.stay-photo{position:absolute;right:0;top:0;width:580px;height:490px;background:linear-gradient(90deg,#eef2f5 0%,#e7d4c2 40%,#e69a3a 58%,#dcdfe3 80%,#f3f5f7 100%)}
.stay-title{position:absolute;left:158px;top:104px;font-size:32px;font-weight:700;color:var(--ink)}
.stay-copy{position:absolute;left:158px;top:158px;width:390px;font-size:19px;line-height:25px;color:var(--ink)}
.stay-copy p+p{margin-top:24px}

/* Organisers */
.team-title{position:absolute;top:2174px;width:100%;text-align:center;color:var(--blue);font-size:28px;font-weight:700}
.organiser{position:absolute;top:2244px;width:424px;height:260px;border-radius:5px;box-shadow:0 0 0 2px #dcdcdc,0 3px 8px rgba(0,0,0,.12);background:var(--white);padding:26px 34px}
.avatar{position:absolute;left:42px;top:34px;width:58px;height:54px;background:linear-gradient(135deg,#4b4640,#a79a8a)}
.org-name{position:absolute;left:116px;top:32px;color:var(--red);font-size:20px;font-weight:700}
.org-social{position:absolute;left:116px;top:64px;display:flex;gap:10px}
.org-social span{width:13px;height:13px;border:2px solid #444;border-radius:3px}
.quote{position:absolute;right:30px;top:34px;color:#c9c9c9;font-size:50px;font-weight:900;line-height:40px}
.org-bio{position:absolute;left:38px;top:104px;right:30px;font-size:12.5px;line-height:22px;color:#444}
.team-dots{position:absolute;top:2546px;left:562px;display:flex;gap:8px}
.team-dots .dot{border-color:#666}
.team-dots .dot.on{background:#666}

/* Footer */
.footer{position:absolute;left:0;top:2612px;width:1200px;height:308px;background:var(--footer-blue);color:var(--white)}
.f-brand{position:absolute;left:162px;top:54px}
.f-brand .brand-name{font-size:29px}
.f-about{position:absolute;left:164px;top:134px;width:260px;font-size:14px;line-height:22px;color:#bfe0f5}
.f-col{position:absolute;top:62px}
.f-col h4{font-size:16px;font-weight:900;margin-bottom:16px}
.f-col li{list-style:none;font-size:14.5px;line-height:26px}
.contact li{display:flex;gap:12px;margin-bottom:14px;line-height:18px}
.social li{display:flex;align-items:center;gap:14px;margin-bottom:8px}
.social li span{width:24px;height:24px;border-radius:50%;background:rgba(255,255,255,.28)}
.bottom-bar{position:absolute;left:0;top:2920px;width:1200px;height:75px;background:var(--footer-blue);border-top:1px solid rgba(255,255,255,.35);color:var(--white);font-size:14.5px;text-align:center;line-height:75px}
</style>
</head>
<body>

<header class="hero">
  <div class="hero-photo" role="img" aria-label="Photo of a smiling man in a checked shirt working at a laptop in a warm office"></div>
  <div class="hero-shade"></div>
  <div class="brand"><div class="brand-name">Makers’ Hollow</div><div class="brand-tag">build. share. grow together</div></div>
  <nav class="main-nav"><span>About Us</span><span>Why Us</span><span>Our Services</span><span>Testimonials</span><span>Contact</span></nav>
  <button class="hero-arrow" style="left:126px" aria-label="Previous"><svg width="52" height="52"><path d="M29 17l-9 9 9 9" fill="none" stroke="#333" stroke-width="3.5"/></svg></button>
  <button class="hero-arrow" style="left:1012px" aria-label="Next"><svg width="52" height="52"><path d="M23 17l9 9-9 9" fill="none" stroke="#333" stroke-width="3.5"/></svg></button>
  <h1 class="hero-title">Welcome to Makers’ Hollow</h1>
  <p class="hero-sub">Duis sed tellus et tortor vestibulum gravida Praesent<br>elementum elit at tellus Curabitur metus</p>
  <div class="hero-dots"><span class="dot"></span><span class="dot on"></span><span class="dot"></span></div>
  <svg class="hero-curve" width="1200" height="90" viewBox="0 0 1200 90">
    <path d="M0 78 Q600 -10 1200 78 L1200 90 L0 90Z" fill="var(--red)"/>
    <path d="M0 86 Q600 0 1200 86 L1200 90 L0 90Z" fill="#fff"/>
  </svg>
</header>

<section>
  <h2 class="intro-title">Makers’ Hollow gives you the space you need to<br>take your side project from idea to reality.</h2>
  <p class="intro-copy">Calling all creatives! Whether you’re a software developer, a UI or UX designer, a product creator or an artworker,<br>you’ll know only too well that great work rarely materialises when you’re in the wrong environment.<br>Phones buzzing. Emails pinging. VoxCall calls incoming...distractions are everywhere – and they do nothing for your<br>motivation. So, if you have a seed of a business idea and need to reclaim some focus, the Makers’ Hollow is for you.<br>Or maybe you’ve created a product, sought a patent and you’re ready – and raring – to go.</p>
  <a class="btn-more">LEARN MORE</a>
</section>

<section class="benefits">
  <svg class="abs" style="left:570px;top:0" width="60" height="16"><path d="M0 0h60L30 16z" fill="#fff"/><path d="M24 4l6 5 6-5" fill="none" stroke="#bbb" stroke-width="1.5"/></svg>
  <h2 class="benefits-title">Join the Retreat and Enjoy:</h2>
  <svg class="chev" style="left:114px" width="22" height="36"><path d="M18 3L5 18l13 15" fill="none" stroke="#fff" stroke-width="4"/></svg>
  <svg class="chev" style="left:1064px" width="22" height="36"><path d="M4 3l13 15L4 33" fill="none" stroke="#fff" stroke-width="4"/></svg>

  <div class="benefit" style="left:160px;top:140px;height:232px;padding-top:26px">
    <svg width="48" height="58" viewBox="0 0 48 58" fill="none" stroke="#fff" stroke-width="2.5"><path d="M24 3a19 19 0 0 0-11 34v8h22v-8A19 19 0 0 0 24 3z"/><path d="M16 50h16M19 55h10M24 22v15M18 22h12"/></svg>
    Three, full days of distraction-free work
  </div>
  <div class="benefit" style="left:384px;top:184px;height:234px;padding-top:44px">
    <svg width="52" height="52" viewBox="0 0 52 52" fill="none" stroke="#fff" stroke-width="2.5"><circle cx="26" cy="26" r="22"/><ellipse cx="26" cy="26" rx="10" ry="22"/><path d="M4 26h44M8 14h36M8 38h36"/></svg>
    A chance to hone your side project away from the office
  </div>
  <div class="benefit" style="left:606px;top:148px;height:234px;padding-top:30px">
    <svg width="64" height="62" viewBox="0 0 64 62" fill="none" stroke="#fff" stroke-width="2.5"><path d="M22 58V46c-10-2-16-10-16-20A18 18 0 0 1 40 18"/><circle cx="44" cy="38" r="8"/><circle cx="44" cy="38" r="14" stroke-dasharray="5 4"/><circle cx="48" cy="10" r="5"/></svg>
    The opportunity to collaborate with likeminded creatives
  </div>
  <div class="benefit" style="left:830px;top:194px;height:234px;padding-top:26px">
    <svg width="64" height="66" viewBox="0 0 64 66" fill="none" stroke="#fff" stroke-width="2.5"><circle cx="32" cy="14" r="8"/><circle cx="32" cy="14" r="12" stroke-dasharray="4 4"/><circle cx="16" cy="38" r="6"/><circle cx="48" cy="38" r="6"/><path d="M4 64V56a12 12 0 0 1 24 0v8M36 64V56a12 12 0 0 1 24 0v8"/></svg>
    Good, honest feedback and insight from fellow attendees
  </div>
</section>

<section class="stay">
  <div class="stay-photo" role="img" aria-label="Photo of a smiling woman in an orange top typing on a laptop at a bright white desk"></div>
  <h2 class="stay-title">Where You’ll be Staying</h2>
  <div class="stay-copy">
    <p>A retreat wouldn’t be a retreat without a calm, peaceful and picturesque location. It’s the reason we’re working hard behind the scenes to find the ideal spot to host you.</p>
    <p>Of course, it’ll have Wi-Fi/4G Internet – but it’ll also be somewhere that will allow for maximum creativity.</p>
  </div>
</section>

<section>
  <h2 class="team-title">Meet Your Retreat Organisers</h2>
  <article class="organiser" style="left:164px">
    <div class="avatar" role="img" aria-label="Portrait photo of Tomas Varga"></div>
    <div class="org-name">Tomas Varga</div>
    <div class="org-social"><span></span><span></span><span></span></div>
    <div class="quote">”</div>
    <p class="org-bio">A software engineer in London, Tomas knows only too well the challenges faced by creatives; it’s the reason he’s organised the Makers’ Hollow, to give everyone the space and time to do their best work. Armed with his trusty camera, photographer Tomas is also a biohacker enthusiast and a thoroughly good egg.</p>
  </article>
  <article class="organiser" style="left:608px">
    <div class="avatar" role="img" aria-label="Portrait photo of Ilka Moreno" style="background:linear-gradient(135deg,#3a2c20,#c8a46a)"></div>
    <div class="org-name">Ilka Moreno</div>
    <div class="org-social"><span></span><span></span><span></span></div>
    <div class="quote">”</div>
    <p class="org-bio">An internationally-certified yoga teacher, Ilka loves connecting with people and discovering how she can help them get the best out of their day – and their work. Giving attendees the time to enjoy some self-care in the form of a spot of gentle yoga, animal lover Ilka will help you unleash those ideas!</p>
  </article>
  <div class="team-dots"><span class="dot"></span><span class="dot on"></span><span class="dot on"></span><span class="dot on"></span></div>
</section>

<footer class="footer">
  <div class="f-brand"><div class="brand-name">Makers’ Hollow</div><div class="brand-tag">build. share. grow together</div></div>
  <p class="f-about">Duis sed tellus et tortor vestibulum gravida Praesent elementum elit at tellus Curabitur metus ipsum</p>
  <div class="f-col contact" style="left:474px">
    <h4>CONTACT US</h4>
    <ul>
      <li><svg width="14" height="18" viewBox="0 0 14 18" fill="none" stroke="#fff" stroke-width="1.6"><path d="M7 17S1 10 1 6.5a6 6 0 0 1 12 0C13 10 7 17 7 17z"/><circle cx="7" cy="6.5" r="2"/></svg><span>42 Larch Row, Suite 3<br>Brookfield 55210 MN</span></li>
      <li><svg width="14" height="16" viewBox="0 0 14 16" fill="none" stroke="#fff" stroke-width="1.6"><path d="M3 1l3 4-2 2c1 2 3 4 5 5l2-2 3 3-2 2C7 15 1 9 1 3z"/></svg><span>555.014.3827</span></li>
      <li><svg width="16" height="14" viewBox="0 0 16 14" fill="none" stroke="#fff" stroke-width="1.6"><rect x="1" y="2" width="14" height="10"/><path d="M1 2l7 6 7-6"/></svg><span>hello@makershollow.example</span></li>
    </ul>
  </div>
  <div class="f-col" style="left:724px">
    <h4>COMPANY</h4>
    <ul><li>Home</li><li>About us</li><li>Services</li><li>Why Us</li><li>Contact</li></ul>
  </div>
  <div class="f-col social" style="left:876px">
    <h4>GET IN TOUCH</h4>
    <ul><li><span></span>Microblog</li><li><span></span>Friends Feed</li><li><span></span>Work Network</li><li><span></span>Photo Stream</li></ul>
  </div>
</footer>
<div class="bottom-bar">Copyright © 2019 All right reserved</div>

</body>
</html>
```